Highlight Document Over Image for Slide

We are seeking a graphic designer to overlay a news article on an image that pertains to the article, aiming for a stylish yet professional appearance. Given the limited resources, we encourage you to use your imagination and go beyond what basic tools like PowerPoint can offer.

```html
<!DOCTYPE html>
<html lang="en">
<head>
<meta charset="utf-8">
<title>Contraband Items Slide</title>
<link href="https://fonts.googleapis.com/css2?family=Tinos:wght@400;700&display=swap" rel="stylesheet">
<style>
  :root {
    --page-bg: #efefef;
    --land-light: #a99466;
    --land-dark: #6f6450;
    --roof-mid: #8a8478;
    --water: #6c6b63;
    --water-deep: #5f5e57;
    --sheet: #ffffff;
    --ink: #111111;
    --rule: #555555;
    --folio: #666666;
  }
  * { margin: 0; padding: 0; box-sizing: border-box; }
  html, body {
    width: 1200px; height: 1200px; overflow: hidden;
    background: var(--page-bg);
  }
  .slide {
    position: absolute;
    left: 25px; top: 242px;
    width: 1155px; height: 650px;
    overflow: hidden;
    box-shadow: 0 4px 12px rgba(0,0,0,0.45);
  }
  .aerial {
    position: absolute; inset: 0;
    background:
      radial-gradient(ellipse 300px 220px at 480px 420px, rgba(120,105,85,0.9), transparent 75%),
      radial-gradient(ellipse 260px 160px at 200px 250px, rgba(150,135,105,0.7), transparent 75%),
      linear-gradient(170deg, var(--land-light) 0%, var(--land-dark) 35%, var(--roof-mid) 55%, var(--water) 72%, var(--water-deep) 100%);
  }
  .article {
    position: absolute;
    left: 715px; top: 125px;
    width: 410px; height: 435px;
    background: var(--sheet);
    box-shadow: 0 0 50px 45px var(--sheet);
    border-radius: 40px;
  }
  .article-inner {
    position: absolute;
    left: 30px; top: 18px;
    width: 365px;
    font-family: "Tinos", "Times New Roman", serif;
    color: var(--ink);
  }
  .article-title {
    font-size: 17.5px; font-weight: 700;
    text-align: center; line-height: 24px;
    margin-left: 20px; width: 340px;
    margin-left: 22px;
  }
  .rule {
    height: 1px; background: var(--rule);
    margin-left: 24px; width: 341px;
  }
  .rule-top { margin-top: 16px; }
  .article-body {
    font-size: 17.5px; line-height: 24px;
    text-align: justify;
    margin-top: 11px; margin-bottom: 14px;
  }
  .folio {
    font-family: "Tinos", "Times New Roman", serif;
    font-weight: 700; font-size: 18px;
    color: var(--folio);
    text-align: center;
    margin-top: 9px; margin-left: 48px;
  }
</style>
</head>
<body>
  <div class="slide">
    <div class="aerial" role="img" aria-label="Aerial view of a waterfront correctional facility with buildings, roads, dry hills and bay water"></div>
    <div class="article">
      <div class="article-inner">
        <h1 class="article-title">INTRODUCTION OR POSSESSION OF CONTRABAND ITEMS</h1>
        <div class="rule rule-top"></div>
        <p class="article-body">Employees shall not introduce or possess unauthorized items such as escape paraphernalia, weapons, facsimiles of weapons, ammunition, wireless communication devices, cell phones, tobacco or facsimiles of tobaccos products (e.g. electronic vapor cigarettes) lighters or any other item not specifically authorized by PD 04.04.100 “Custody, Security and Safety Systems (Exempt)”, OP 04.04.100 “Gate Security” or facility operating procedure in any facility where offenders are housed. Employees are responsible for any item in their</p>
        <div class="rule"></div>
        <div class="folio">36</div>
      </div>
    </div>
  </div>
</body>
</html>
```